Computer consultant business card

Bexil Software is a newly started computer consulting company. It's a small one-man company that provides mostly Vornix applications but also websites in collaboration with designers. I'm running this company on the side of full time university studies.

I want the final design to be clean and memorable. Be creative! :)

Some inspiration:
http://www.pixelmarta.com/design/48317
http://www.pixelmarta.com/design/2739164/business-card-design-by-frostlynk
http://www.pixelmarta.com/design/604281/business-card-design-by-koralind-vestrabanu

See attachment for my company logo.
Updates

I would like to thank everyone for submitting! I'll need a couple of days to review and ultimately select a design.

Target Market(s)

Non-technical entrepreneurs and small companies.

Industry/Entity Type

University

Requirements
Must have
• My company logo.
In any way, both colors from my logo.
First- and last name, e-mail and phone number.
Double-sided design.
Nice to have
• Something creative with the symbol in my logo

```html
<!DOCTYPE html>
<html lang="en">
<head>
<meta charset="utf-8">
<title>Trelvo – Business Card</title>
<link href="https://fonts.googleapis.com/css2?family=Jost:wght@400;500;600&display=swap" rel="stylesheet">
<style>
  :root {
    --stage: #c9a877;
    --label: #2a2622;
    --ink: #333335;
    --brand-blue: #4472b9;
    --paper: #ffffff;
    --night: #050505;
    --slate-top: #2f3038;
    --slate-glow: #4d5f8c;
    --muted: #555555;
  }
  * { box-sizing: border-box; margin: 0; padding: 0; }
  html, body { width: 1200px; height: 788px; overflow: hidden; }
  body {
    position: relative;
    background: var(--stage);
    font-family: "Jost", "Futura", sans-serif;
    color: var(--ink);
  }
  .side-label {
    position: absolute;
    width: 526px;
    text-align: center;
    font-size: 20px;
    font-weight: 400;
    color: var(--label);
  }
  .card {
    position: absolute;
    width: 526px;
    height: 300px;
    border-radius: 22px;
    overflow: hidden;
    box-shadow: 0 4px 10px rgba(0,0,0,0.35);
  }
  .card--front { left: 53px; top: 74px; background: var(--paper); }
  .card--back-light { left: 622px; top: 74px; background: var(--paper); }
  .card--back-dark { left: 53px; top: 446px; background: var(--night); }
  .card--back-slate {
    left: 622px; top: 446px;
    background: radial-gradient(ellipse 90% 110% at 45% 100%, var(--slate-glow), var(--slate-top) 75%);
  }
  .texture {
    position: absolute; inset: 0;
    background:
      radial-gradient(ellipse 34% 40% at 30% 0%, rgba(120,120,120,0.45), transparent 70%),
      radial-gradient(ellipse 30% 42% at 78% 95%, rgba(140,135,140,0.5), transparent 70%);
  }

  .header-band {
    position: absolute; left: 0; right: 0; top: 39px;
    display: flex; align-items: center; height: 78px;
  }
  .band-dark { width: 59px; height: 39px; background: var(--ink); }
  .band-blue { flex: 1; height: 39px; background: var(--brand-blue); }
  .wordmark {
    display: flex; align-items: center;
    font-weight: 500; line-height: 1;
  }
  .wordmark__dot { border-radius: 50%; background: var(--brand-blue); flex: none; }
  .wordmark--small { gap: 14px; padding: 0 8px 0 6px; font-size: 54px; color: var(--ink); }
  .wordmark--small .wordmark__dot { width: 70px; height: 70px; }
  .wordmark--large {
    position: absolute; left: 0; right: 0; top: 92px;
    justify-content: center; gap: 22px; font-size: 76px;
  }
  .wordmark--large .wordmark__dot { width: 100px; height: 100px; }
  .wordmark--ink { color: var(--ink); }
  .wordmark--white { color: #ffffff; }

  .contact { position: absolute; left: 55px; top: 186px; }
  .contact__name { font-size: 17px; font-weight: 600; line-height: 22px; }
  .contact__role { font-size: 12px; line-height: 16px; color: var(--muted); margin-top: 3px; }
  .contact__line {
    display: flex; align-items: center; gap: 10px;
    font-size: 15px; line-height: 21px;
  }
  .contact__role + .contact__line { margin-top: 4px; }
  .contact__line svg { width: 12px; height: 12px; fill: var(--ink); }

  .site {
    position: absolute; left: 0; right: 0; top: 250px;
    text-align: center; font-size: 17px; letter-spacing: 3.2px;
  }
  .site--ink { color: var(--ink); }
  .site--white { color: #ffffff; }
</style>
</head>
<body>
  <div class="side-label" style="left:57px; top:34px;">Front</div>
  <div class="side-label" style="left:633px; top:34px;">Back - 1</div>
  <div class="side-label" style="left:57px; top:404px;">Back - 2</div>
  <div class="side-label" style="left:633px; top:404px;">Back - 3</div>

  <section class="card card--front">
    <div class="header-band">
      <div class="band-dark"></div>
      <div class="wordmark wordmark--small"><span class="wordmark__dot"></span>trelvo</div>
      <div class="band-blue"></div>
    </div>
    <div class="contact">
      <p class="contact__name">First Name + Last Name</p>
      <p class="contact__role">Designation</p>
      <p class="contact__line">
        <svg viewBox="0 0 12 12" aria-hidden="true"><path d="M3 1 L5 3.5 L4 5 Q5 7 7 8 L8.5 7 L11 9 L9.5 11 Q4 10.5 1 3 Z"/></svg>
        +12 345 6789
      </p>
      <p class="contact__line">
        <svg viewBox="0 0 12 12" aria-hidden="true"><path d="M1 3 H11 V10 H1 Z M1.5 3.5 L6 7 L10.5 3.5" fill="none" stroke="#333335" stroke-width="1.3"/></svg>
        info@website.com
      </p>
    </div>
  </section>

  <section class="card card--back-light">
    <div class="wordmark wordmark--large wordmark--ink"><span class="wordmark__dot"></span>trelvo</div>
    <p class="site site--ink">www.website.com</p>
  </section>

  <section class="card card--back-dark">
    <div class="texture" role="img" aria-label="Perforated metal dot texture in the corners"></div>
    <div class="wordmark wordmark--large wordmark--white"><span class="wordmark__dot"></span>trelvo</div>
    <p class="site site--white">www.website.com</p>
  </section>

  <section class="card card--back-slate">
    <div class="wordmark wordmark--large wordmark--white"><span class="wordmark__dot"></span>trelvo</div>
    <p class="site site--white">www.website.com</p>
  </section>
</body>
</html>
```